Real Estate Business Card

On the front side I want to have my info, my brokerage info.
On the back side I want have my complany’s logo, website and Facebook link. I will provide all this once I select a design.

I would like to see Black background and gold text, Dark Blue and gold text and White and blue text designs

Font styles to use
Sans Serif
Script

```html
<!DOCTYPE html>
<html lang="en">
<head>
<meta charset="utf-8">
<title>Northpeak Real Estate – Business Card</title>
<link href="https://fonts.googleapis.com/css2?family=Roboto:wght@400;500&family=Roboto+Condensed:wght@700&display=swap" rel="stylesheet">
<style>
  :root {
    --backdrop: #2b2b2c;
    --card: #1b1b1c;
    --gold: #ecc65a;
    --brand-grey: #b9bcc4;
    --web-grey: #6f7682;
    --accent-red: #d2343a;
  }
  * { box-sizing: border-box; margin: 0; padding: 0; }
  html, body {
    width: 1200px; height: 900px; overflow: hidden;
    background: var(--backdrop);
  }
  .canvas {
    position: relative; width: 1200px; height: 900px;
    font-family: "Roboto", Arial, sans-serif;
  }
  .card {
    position: absolute; left: 280px; width: 640px; height: 366px;
    background: var(--card);
    box-shadow: 0 10px 30px rgba(0,0,0,.45);
  }
  .card--brand { top: 60px; }
  .card--contact { top: 474px; }

  /* Brand side */
  .brand {
    position: absolute; left: 0; right: 0; top: 128px;
    display: flex; align-items: center; justify-content: center; gap: 14px;
  }
  .brand__square { width: 26px; height: 26px; background: var(--accent-red); }
  .brand__name {
    font-family: "Roboto Condensed", Arial, sans-serif; font-weight: 700;
    font-size: 44px; letter-spacing: 1px; text-transform: uppercase;
    color: var(--brand-grey);
  }
  .brand__web {
    position: absolute; left: 0; right: 0; top: 266px; text-align: center;
    font-size: 17px; letter-spacing: 7px; color: var(--web-grey);
  }

  /* Contact side */
  .person {
    position: absolute; right: 382px; top: 112px; text-align: right;
    color: var(--gold);
  }
  .person__name {
    font-family: "Roboto Condensed", Arial, sans-serif; font-weight: 700;
    font-size: 38px; line-height: 1; text-transform: uppercase;
  }
  .person__title {
    margin-top: 8px; font-size: 17px; font-weight: 500; text-transform: uppercase;
  }
  .divider {
    position: absolute; left: 274px; top: 96px; width: 2px; height: 128px;
    background: var(--gold);
  }
  .contacts {
    position: absolute; left: 292px; top: 98px; list-style: none;
    color: var(--gold); font-size: 17px;
  }
  .contacts li { display: flex; align-items: center; gap: 9px; height: 24px; }
  .contacts svg { width: 15px; height: 15px; fill: var(--gold); flex: none; }
  .address {
    position: absolute; left: 36px; top: 280px;
    display: flex; align-items: center; gap: 10px;
    color: var(--gold); font-size: 18px;
  }
  .address svg { width: 14px; height: 19px; fill: var(--gold); }
</style>
</head>
<body>
<div class="canvas">

  <section class="card card--brand">
    <div class="brand">
      <span class="brand__square"></span>
      <span class="brand__name">Northpeak Real Estate</span>
    </div>
    <p class="brand__web">www.northpeakhomes.com</p>
  </section>

  <section class="card card--contact">
    <div class="person">
      <p class="person__name">Daniel Reyes</p>
      <p class="person__title">CEO/Founder</p>
    </div>
    <span class="divider"></span>
    <ul class="contacts">
      <li><svg viewBox="0 0 16 16"><path d="M3.5 1 6 1.5 7 5 5.3 6.3a9 9 0 0 0 4.4 4.4L11 9l3.5 1 .5 2.5L13 15C6.5 14.5 1.5 9.5 1 3Z"/></svg>555 014 7720</li>
      <li><svg viewBox="0 0 16 16"><path d="M4 0h8a1 1 0 0 1 1 1v14a1 1 0 0 1-1 1H4a1 1 0 0 1-1-1V1a1 1 0 0 1 1-1Zm1 2v10h6V2Zm3 11a1 1 0 1 0 0 2 1 1 0 0 0 0-2Z"/></svg>555 027 3186</li>
      <li><svg viewBox="0 0 16 16"><path d="M4 1h7l2 2v3H4ZM1 7h14v6h-2v2H3v-2H1Zm4 4v3h6v-3Z"/></svg>555 039 6452</li>
      <li><svg viewBox="0 0 16 16"><path d="M1 3h14v1L8 9 1 4Zm0 2.5 7 5 7-5V13H1Z"/></svg>daniel@northpeakhomes.com</li>
      <li><svg viewBox="0 0 16 16"><path d="M8 1a7 7 0 1 0 0 14A7 7 0 0 0 8 1Zm-1 2.5 2 1-1 2 2 1 1 3-2 2-1-2-2-1V7L4.5 5.5A5 5 0 0 1 7 3.5Z"/></svg>www.northpeakhomes.com</li>
    </ul>
    <p class="address">
      <svg viewBox="0 0 14 19"><path d="M7 0a7 7 0 0 0-7 7c0 5 7 12 7 12s7-7 7-12a7 7 0 0 0-7-7Zm0 4.5a2.5 2.5 0 1 1 0 5 2.5 2.5 0 0 1 0-5Z"/></svg>
      1420 Birchwood Drive, Juneau, Alaska 99801
    </p>
  </section>

</div>
</body>
</html>
```